Climbing Gear Company Stationary Design

We need some new stationary to standardise our business.
We require:

Business Card
A4 Letterhead
With complements slip

Our business is a Distributor and retailer of rock climbing equipment throughout Australia.
We need to the stationary (business card in particular) to reflect this.

Target Market(s)

customers, other retail outlets, overseas manufacturers.

Industry/Entity Type

Business

Requirements
Must have
• company logo
website url- www.ridgetopgearworks.com.au
email - mark@ridgetopgearworks.com
Business Address: Unit 3, 14-16 Marlowe Street, Coffs Harbour, NSW, 2371
Phone: 0438 627 194
my Name (on Business card) - Gordon Pellimore
use of Blue colour in our logo

```html
<!DOCTYPE html>
<html lang="en">
<head>
<meta charset="utf-8">
<title>Ridgetop Gearworks – Business Card</title>
<link rel="stylesheet" href="https://fonts.googleapis.com/css2?family=Source+Sans+3:wght@400;600;700&display=swap">
<style>
  :root {
    --brand-blue: #1f4188;
    --text-grey: #555559;
    --card-white: #ffffff;
    --backdrop: #e9e9e7;
    --card-edge: #b9b9b9;
  }
  * { box-sizing: border-box; margin: 0; padding: 0; }
  html, body {
    width: 1200px; height: 1039px; overflow: hidden;
    background: var(--backdrop);
    font-family: "Source Sans 3", sans-serif;
  }
  .canvas { position: relative; width: 1200px; height: 1039px; }

  .card {
    position: absolute;
    width: 722px; height: 412px;
    background: var(--card-white);
    border: 1px solid var(--card-edge);
    overflow: hidden;
  }
  .card--front { left: 69px; top: 62px; }
  .card--back  { left: 382px; top: 539px; }

  .brand { position: absolute; left: 0; right: 0; text-align: center; }
  .brand__name {
    display: block;
    color: var(--brand-blue);
    font-weight: 700;
    font-size: 48px;
    line-height: 1;
    letter-spacing: 1px;
  }
  .brand__tagline {
    display: block;
    margin-top: 14px;
    color: var(--brand-blue);
    font-weight: 400;
    font-size: 17px;
    letter-spacing: 3.6px;
  }
  .card--front .brand { top: 60px; }
  .card--back .brand  { top: 161px; }

  .holder {
    position: absolute; top: 180px; left: 0; right: 0;
    text-align: center;
    color: var(--brand-blue);
    font-weight: 700; font-size: 23px;
  }
  .address {
    position: absolute; top: 235px; left: 0; right: 0;
    text-align: center;
    color: var(--text-grey); font-size: 18px;
  }
  .contact {
    position: absolute; top: 267px; left: 0; right: 0;
    display: flex; justify-content: center; align-items: center; gap: 10px;
    color: var(--text-grey); font-size: 18px;
  }
  .contact__item { display: inline-flex; align-items: center; gap: 6px; }
  .contact__icon { fill: var(--text-grey); }

  .footer-rule {
    position: absolute; left: 0; right: 0; top: 330px;
    height: 3px; background: var(--brand-blue);
  }
  .footer-band {
    position: absolute; left: 0; right: 0; top: 340px; bottom: 0;
    background: var(--brand-blue);
  }

  .web--front {
    position: absolute; right: 24px; top: 362px;
    color: var(--card-white);
    font-size: 19px; letter-spacing: 1.2px;
  }
  .web--back {
    position: absolute; left: 0; right: 0; top: 350px;
    text-align: center;
    color: var(--text-grey);
    font-size: 18px; letter-spacing: 3px;
  }
</style>
</head>
<body>
<main class="canvas">

  <section class="card card--front" aria-label="Business card front">
    <div class="brand">
      <span class="brand__name">RIDGETOP GEARWORKS</span>
      <span class="brand__tagline">THE ROPE•THE ROCK•THE JOURNEY</span>
    </div>

    <p class="holder">Gordon Pellimore</p>
    <p class="address">Unit 3, 14-16 Marlowe Street, Coffs Harbour, NSW, 2371</p>
    <p class="contact">
      <span class="contact__item">
        <svg class="contact__icon" width="14" height="14" viewBox="0 0 24 24" aria-hidden="true">
          <path d="M6.6 10.8a15.1 15.1 0 0 0 6.6 6.6l2.2-2.2a1 1 0 0 1 1-.25 11.4 11.4 0 0 0 3.6.57 1 1 0 0 1 1 1V20a1 1 0 0 1-1 1A17 17 0 0 1 3 4a1 1 0 0 1 1-1h3.5a1 1 0 0 1 1 1c0 1.25.2 2.45.57 3.57a1 1 0 0 1-.25 1z"/>
        </svg>
        0438 627 194
      </span>
      <span class="contact__item">
        <svg class="contact__icon" width="13" height="10" viewBox="0 0 13 10" aria-hidden="true">
          <rect x="0" y="0" width="13" height="10"/>
          <path d="M0,0 L6.5,5 L13,0" fill="none" stroke="var(--card-white)" stroke-width="1.2"/>
        </svg>
        mark@ridgetopgearworks.com
      </span>
    </p>

    <div class="footer-rule"></div>
    <div class="footer-band"></div>
    <p class="web--front">www.ridgetopgearworks.com.au</p>
  </section>

  <section class="card card--back" aria-label="Business card back">
    <div class="brand">
      <span class="brand__name">RIDGETOP GEARWORKS</span>
      <span class="brand__tagline">THE ROPE•THE ROCK•THE JOURNEY</span>
    </div>
    <p class="web--back">www.ridgetopgearworks.com.au</p>
  </section>

</main>
</body>
</html>
```